Beautiful design for wordpress

I need a beautiful, colourful and feminine website. My business is called 'The Velvet Lantern', and I sell crystals, books, CD's, pendulums and other metaphysical items. I also provide Reiki (energy healing).
I want this design to be eye catching and inspire happiness and joy in those who see it. And I would love to see the use of the logo and its colours :)
Please add these on the web design: Home, About, Online store, Blog

Industry/Entity Type

Business

Requirements
Must have
• Colourful and playful, must use the logo somewhere, have the words on a menu saying 'Home, Blog, Online store and about' (or similar to those)And the design must stand out!
Should not have
• grey, brown and other boring colours.

```html
<!DOCTYPE html>
<html lang="en">
<head>
<meta charset="utf-8">
<title>The Velvet Lantern — Crystals, Books &amp; Reiki</title>
<link href="https://fonts.googleapis.com/css2?family=Open+Sans:wght@400;600;700&family=Lora:wght@400;700&display=swap" rel="stylesheet">
<style>
  :root{
    --pink:#f36f8b;
    --pink-dark:#e0506f;
    --pink-soft:#f9a9ba;
    --orange:#f7941d;
    --green:#8cc63f;
    --purple:#9d6bd0;
    --ink:#444;
    --muted:#999;
    --line:#e4e4e4;
    --white:#fff;
    --hero-deep:#1c2a4a;
    --hero-mid:#3b5a86;
  }
  *{box-sizing:border-box;margin:0;padding:0}
  html,body{width:764px;height:1200px;overflow:hidden}
  body{font-family:"Open Sans",Arial,sans-serif;color:var(--ink);background:var(--white);position:relative}

  /* Header */
  .site-header{position:absolute;top:0;left:0;width:764px;height:112px}
  .brand{position:absolute;left:40px;top:24px;display:flex;align-items:center;gap:8px}
  .brand-dot{width:22px;height:22px;border-radius:50%;background:var(--pink)}
  .brand-name{font-family:"Open Sans",Arial,sans-serif;font-weight:700;font-size:17px;color:var(--pink);line-height:1.1;width:110px}
  .account-links{position:absolute;right:60px;top:10px;font-size:10px;color:#666}
  .account-links span{margin:0 4px;color:#bbb}
  .search{position:absolute;right:70px;top:42px;width:180px;height:22px;border:1px solid var(--line);display:flex}
  .search-field{flex:1;font-size:9px;color:#bbb;padding:4px 6px}
  .search-btn{width:22px;background:var(--orange);display:flex;align-items:center;justify-content:center}
  .main-nav{position:absolute;left:225px;top:80px;width:539px;height:30px;background:var(--pink);display:flex}
  .main-nav a{color:var(--white);text-decoration:none;font-size:11px;font-weight:600;padding:0 18px;line-height:30px;letter-spacing:.3px}
  .main-nav a.active{background:var(--pink-dark)}

  /* Hero */
  .hero{position:absolute;top:112px;left:0;width:764px;height:262px;
    background:radial-gradient(circle at 70% 45%,#c9d8ec 0%,#8ea9cf 18%,var(--hero-mid) 42%,var(--hero-deep) 80%)}
  .hero-text{position:absolute;left:58px;top:102px;color:var(--white);font-family:"Lora",Georgia,serif}
  .hero-title{font-size:22px;font-weight:400}
  .hero-sub{font-size:20px;margin-top:2px}
  .hero-dots{position:absolute;left:58px;bottom:16px;display:flex;gap:5px}
  .hero-dots i{width:6px;height:6px;border-radius:50%;background:rgba(255,255,255,.5)}
  .hero-dots i:first-child{background:var(--white)}

  /* Welcome */
  .welcome{position:absolute;top:412px;left:58px;width:260px}
  .welcome h2{font-family:"Lora",Georgia,serif;font-weight:400;font-size:19px;color:var(--green);margin-bottom:10px}
  .welcome p{font-size:8.5px;line-height:1.55;color:#777;margin-bottom:8px}
  .promo{position:absolute;top:412px;width:168px;height:135px}
  .promo-shop{left:333px}
  .promo-offers{left:510px}
  .promo-visual{height:90px}
  .promo-shop .promo-visual{background:linear-gradient(135deg,#9b8a7c,#5e5a66)}
  .promo-offers .promo-visual{background:linear-gradient(135deg,#d9c9ef,#a58bd8)}
  .promo-caption{height:45px;padding:6px 8px;color:var(--white)}
  .promo-shop .promo-caption{background:var(--pink)}
  .promo-offers .promo-caption{background:var(--purple)}
  .promo-caption h3{font-size:12px;font-weight:600}
  .promo-caption p{font-size:7px;margin-top:3px;opacity:.9}

  /* Products */
  .products{position:absolute;top:565px;left:58px;width:648px;display:grid;grid-template-columns:repeat(4,162px);grid-auto-rows:176px;border-top:1px solid var(--line);border-left:1px solid var(--line)}
  .product{border-right:1px solid var(--line);border-bottom:1px solid var(--line);padding:10px 10px 8px}
  .product-visual{height:90px;margin:0 10px 10px;border-radius:4px}
  .v-disc{background:radial-gradient(circle,#f4f4f4 20%,#c9ccd6 55%,#fff 70%)}
  .v-crystal{background:linear-gradient(160deg,#7fb0f0,#274a9c)}
  .v-book{background:linear-gradient(160deg,#5e7e3c,#2f4a1f)}
  .v-sticks{background:linear-gradient(90deg,#b4716a,#6e3c3a)}
  .v-pendants{background:linear-gradient(160deg,#d5b4e6,#8c4aa8)}
  .v-book2{background:linear-gradient(160deg,#ece6c8,#b9ae80)}
  .v-pendulum{background:linear-gradient(160deg,#f3d98a,#c8962d)}
  .v-bracelet{background:linear-gradient(160deg,#8fd9c9,#e57fa0)}
  .product-name{font-size:11px;color:#555}
  .product-desc{font-size:6.5px;color:var(--muted);margin:2px 0 6px;line-height:1.4}
  .product-foot{display:flex;align-items:center;justify-content:space-between}
  .price{font-size:15px;color:var(--pink);font-weight:600}
  .add-cart{background:var(--pink);color:var(--white);font-size:6.5px;padding:3px 6px;border-radius:2px}

  /* Footer */
  .site-footer{position:absolute;top:920px;left:0;width:764px;height:280px;background:linear-gradient(180deg,var(--pink-soft),var(--pink) 85%)}
  .footer-cols{position:absolute;top:18px;left:58px;display:flex;gap:0}
  .footer-col{width:140px}
  .footer-col h4{color:var(--white);font-size:12px;font-weight:600;margin-bottom:6px}
  .footer-col li{list-style:none;color:var(--white);font-size:7px;line-height:1.7;opacity:.95}
  .social{position:absolute;top:18px;left:620px}
  .social h4{color:var(--white);font-size:12px;font-weight:600;margin-bottom:8px}
  .social-row{display:flex;gap:5px}
  .social-row i{width:16px;height:16px;border-radius:50%;background:var(--white)}
  .copyright{position:absolute;bottom:10px;left:58px;font-size:7px;color:var(--white);opacity:.9}
</style>
</head>
<body>

<header class="site-header">
  <div class="brand">
    <span class="brand-dot"></span>
    <span class="brand-name">The Velvet Lantern</span>
  </div>
  <div class="account-links">My Account<span>|</span>My Cart<span>|</span>Wish List<span>|</span>Support</div>
  <div class="search">
    <div class="search-field">Search</div>
    <div class="search-btn">
      <svg width="10" height="10" viewBox="0 0 10 10"><circle cx="4" cy="4" r="3" fill="none" stroke="#fff" stroke-width="1.4"/><line x1="6.2" y1="6.2" x2="9" y2="9" stroke="#fff" stroke-width="1.4"/></svg>
    </div>
  </div>
  <nav class="main-nav">
    <a class="active" href="#">HOME</a>
    <a href="#">ABOUT</a>
    <a href="#">ONLINE STORE</a>
    <a href="#">BLOG</a>
    <a href="#">CONTACT US</a>
  </nav>
</header>

<section class="hero" role="img" aria-label="Photograph of clear quartz crystal points on a deep blue background">
  <div class="hero-text">
    <div class="hero-title">Pendulums and Metaphysical</div>
    <div class="hero-sub">Aliquam necerat purus</div>
  </div>
  <div class="hero-dots"><i></i><i></i><i></i></div>
</section>

<section class="welcome">
  <h2>Welcome to Velvet Lantern</h2>
  <p>Crystals, pendulums, books and music gathered with love to bring light, balance and joy into your everyday life. Explore our shop, book a gentle Reiki session and discover the tools that speak to your spirit.</p>
  <p>Every piece is cleansed and blessed before it leaves our lantern lit studio.</p>
</section>

<div class="promo promo-shop">
  <div class="promo-visual" role="img" aria-label="Photograph of a raw crystal cluster"></div>
  <div class="promo-caption"><h3>Online Shop</h3><p>Browse crystals, books and more</p></div>
</div>
<div class="promo promo-offers">
  <div class="promo-visual" role="img" aria-label="Photograph of amethyst crystals"></div>
  <div class="promo-caption"><h3>Special Offers</h3><p>Seasonal deals on healing tools</p></div>
</div>

<section class="products">
  <article class="product"><div class="product-visual v-disc" role="img" aria-label="Meditation music CD"></div><div class="product-name">Product Name</div><div class="product-desc">Cleansed by hand, ready for your altar.</div><div class="product-foot"><span class="price">$25.99</span><span class="add-cart">Add to Cart</span></div></article>
  <article class="product"><div class="product-visual v-crystal" role="img" aria-label="Blue crystal cluster"></div><div class="product-name">Product Name</div><div class="product-desc">Cleansed by hand, ready for your altar.</div><div class="product-foot"><span class="price">$25.99</span><span class="add-cart">Add to Cart</span></div></article>
  <article class="product"><div class="product-visual v-book" role="img" aria-label="Spiritual book cover"></div><div class="product-name">Product Name</div><div class="product-desc">Cleansed by hand, ready for your altar.</div><div class="product-foot"><span class="price">$25.99</span><span class="add-cart">Add to Cart</span></div></article>
  <article class="product"><div class="product-visual v-sticks" role="img" aria-label="Set of incense sticks"></div><div class="product-name">Product Name</div><div class="product-desc">Cleansed by hand, ready for your altar.</div><div class="product-foot"><span class="price">$25.99</span><span class="add-cart">Add to Cart</span></div></article>
  <article class="product"><div class="product-visual v-pendants" role="img" aria-label="Gemstone pendulum pendants"></div><div class="product-name">Product Name</div><div class="product-desc">Cleansed by hand, ready for your altar.</div><div class="product-foot"><span class="price">$25.99</span><span class="add-cart">Add to Cart</span></div></article>
  <article class="product"><div class="product-visual v-book2" role="img" aria-label="Self help book cover"></div><div class="product-name">Product Name</div><div class="product-desc">Cleansed by hand, ready for your altar.</div><div class="product-foot"><span class="price">$25.99</span><span class="add-cart">Add to Cart</span></div></article>
  <article class="product"><div class="product-visual v-pendulum" role="img" aria-label="Brass pendulum on a chain"></div><div class="product-name">Product Name</div><div class="product-desc">Cleansed by hand, ready for your altar.</div><div class="product-foot"><span class="price">$25.99</span><span class="add-cart">Add to Cart</span></div></article>
  <article class="product"><div class="product-visual v-bracelet" role="img" aria-label="Colourful gemstone bead bracelet"></div><div class="product-name">Product Name</div><div class="product-desc">Cleansed by hand, ready for your altar.</div><div class="product-foot"><span class="price">$25.99</span><span class="add-cart">Add to Cart</span></div></article>
</section>

<footer class="site-footer">
  <div class="footer-cols">
    <div class="footer-col"><h4>Company</h4><ul><li>About Us</li><li>Our Story</li><li>Reiki Sessions</li><li>Gift Cards</li><li>Contact Us</li></ul></div>
    <div class="footer-col"><h4>Features</h4><ul><li>New Arrivals</li><li>Crystal Guide</li><li>Best Sellers</li><li>Music Library</li><li>Healing Kits</li></ul></div>
    <div class="footer-col"><h4>Resources</h4><ul><li>Reiki Basics</li><li>Pendulum Tips</li><li>Reading List</li><li>Moon Calendar</li><li>Care Guide</li></ul></div>
    <div class="footer-col"><h4>Support</h4><ul><li>Shipping Info</li><li>Easy Returns</li><li>Order Status</li><li>Payment Options</li><li>Common Questions</li></ul></div>
  </div>
  <div class="social">
    <h4>Get in Touch</h4>
    <div class="social-row"><i></i><i></i><i></i><i></i></div>
  </div>
  <div class="copyright">© 2024 The Velvet Lantern. All rights reserved.</div>
</footer>

</body>
</html>
```